Orvane Mechanical - Letterhead

We are a plumbing and hvac company based in Calgary. This letterhead will be on our quotes, invoices, preventative maintenance proposals etc.

```html
<!DOCTYPE html>
<html lang="en">
<head>
<meta charset="utf-8">
<title>Orvane Mechanical – Letterhead</title>
<link href="https://fonts.googleapis.com/css2?family=Lato:wght@400;900&family=Roboto+Condensed:wght@300&display=swap" rel="stylesheet">
<style>
  :root {
    --brand-blue: #1c6fbb;
    --brand-orange: #ef5a24;
    --ink: #4a4a4a;
    --paper: #ffffff;
    --backdrop: #d6d6d6;
  }
  * { box-sizing: border-box; margin: 0; padding: 0; }
  html, body {
    width: 1056px; height: 1200px; overflow: hidden;
    background: var(--backdrop);
  }
  .sheet {
    position: absolute; left: 123px; top: 27px;
    width: 810px; height: 1145px;
    background: var(--paper);
    overflow: hidden;
  }
  .brand {
    position: absolute; left: 75px; top: 112px;
    display: flex; align-items: center; gap: 10px;
  }
  .brand-dot {
    width: 22px; height: 22px; border-radius: 50%;
    background: var(--brand-orange);
  }
  .brand-name {
    font-family: "Lato", sans-serif; font-weight: 900;
    font-size: 28px; letter-spacing: 0.5px;
    color: var(--brand-blue); text-transform: uppercase;
  }
  .contact {
    position: absolute; left: 586px; top: 58px;
    font-family: "Lato", sans-serif; font-size: 13.5px; font-style: normal;
    color: var(--brand-blue); line-height: 17px;
  }
  .contact-address { margin-bottom: 8px; }
  .contact-line { display: flex; align-items: center; gap: 13px; height: 19.5px; }
  .contact-line svg { width: 12px; height: 12px; flex: none; }
  .accent { color: var(--brand-orange); }
  .letter {
    position: absolute; left: 75px; top: 326px; width: 657px;
    font-family: "Roboto Condensed", sans-serif; font-weight: 300;
    font-size: 18px; line-height: 28.3px; color: var(--ink);
    text-align: justify;
  }
  .letter p { margin-bottom: 28px; }
  .letter .salutation { margin-bottom: 25px; }
  .closing {
    position: absolute; left: 75px; top: 898px;
    font-family: "Roboto Condensed", sans-serif; font-weight: 300;
    font-size: 18px; color: var(--ink);
  }
  .signature {
    position: absolute; left: 70px; top: 936px; width: 66px; height: 45px;
    background: linear-gradient(135deg, #e3eef8, #cfe1f2);
    border-radius: 4px;
  }
  .footer-rule {
    position: absolute; left: 0; bottom: 22px; width: 810px; height: 3px;
    background: var(--brand-orange);
  }
  .footer-bar {
    position: absolute; left: 0; bottom: 0; width: 810px; height: 16px;
    background: var(--brand-blue);
  }
</style>
</head>
<body>
  <main class="sheet">
    <header>
      <div class="brand">
        <span class="brand-dot"></span>
        <span class="brand-name">Orvane Mechanical</span>
      </div>
      <address class="contact">
        <div class="contact-address">1234 First Line Address<br>5678 Second Line Address</div>
        <div class="contact-line">
          <svg viewBox="0 0 12 12"><path d="M2.5 1 L4.5 1 L5.3 3.6 L4 4.6 C4.6 6 5.9 7.3 7.3 7.9 L8.3 6.6 L11 7.4 L11 9.5 C11 10.3 10.3 11 9.5 11 C5 10.6 1.4 7 1 2.5 C1 1.7 1.7 1 2.5 1 Z" fill="var(--brand-orange)"/></svg>
          <span>1234567890</span>
        </div>
        <div class="contact-line">
          <svg viewBox="0 0 12 12"><rect x="0.5" y="2" width="11" height="8" fill="var(--brand-orange)"/><path d="M0.5 2 L6 6.5 L11.5 2 M0.5 10 L4.5 5.5 M11.5 10 L7.5 5.5" stroke="#fff" stroke-width="0.9" fill="none"/></svg>
          <span>info@yourmail.com</span>
        </div>
        <div class="contact-line">
          <svg viewBox="0 0 12 12"><g fill="none" stroke="var(--brand-orange)" stroke-width="0.9"><circle cx="6" cy="6" r="5"/><ellipse cx="6" cy="6" rx="2.2" ry="5"/><path d="M1 6 H11 M2 3.3 H10 M2 8.7 H10"/></g></svg>
          <span>www.<span class="accent">yourwebsite</span>.com</span>
        </div>
      </address>
    </header>

    <section class="letter">
      <p class="salutation">Dear Sir/Mam,</p>
      <p>Contrary to popular belief, Lorem Ipsum is not simply random text. It has roots in a piece of classical Latin literature from 45 BC, making it over 2000 years old. Daniel Hartwell, a Latin professor at Whitcombe College in Virginia, looked up one of the more obscure Latin words, consectetur.</p>
      <p>Lorem Ipsum comes from sections 1.10.32 and 1.10.33 of "de Finibus Bonorum et Malorum" (The Extremes of Good and Evil) by Aurelian, written in 45 BC. This book is a treatise on the theory of ethics, very popular during the Renaissance. The first line of Lorem Ipsum.</p>
      <p>The standard chunk of Lorem Ipsum used since the 1500s is reproduced below for those interested. Sections 1.10.32 and 1.10.33 from "de Finibus Bonorum et Malorum" by Aurelian are also reproduced in their exact original.</p>
      <p>The standard chunk of Lorem Ipsum used since the 1500s is reproduced below for those interested.</p>
    </section>

    <div class="closing">Best Regards</div>
    <div class="signature" role="img" aria-label="Handwritten signature of the sender"></div>

    <footer>
      <div class="footer-rule"></div>
      <div class="footer-bar"></div>
    </footer>
  </main>
</body>
</html>
```